B2B flyer solution for charging infrastructures (One-Pager Din A4, double-sided)

We need a professional design for our flyer in format Din A4/both sides.
Attached you will find the content for the flyer, but we are looking for a modern, professional design.

Some background/context information:
- the product is about a solution for charging and billing of charging infrastructures (for electric cars) in companies
- target group: companies, esp. facility managers, fleet managers, controlling, CTO, CEO
- should be printed and available online
- our website (and most of our current design work): https://wendavo-netz.de

In the files you will find:
- photos of reference implementations of our solution (should be included in the flyer)
- stock photos (we are using the one you will find in the current flyer on our presentations, maybe you can use it too to keep some corporate identity.
- our logo
- the current flyer as PDF and as PowerPoint
- a sample presentation we also need for customer communication

It would be nice if the design will align with the existing design work, but bring fresh aspects and will be up-to-date and professional.

Target Market(s)

B2B, companies, fleet managers, facility managers, CTO, CIO

Industry/Entity Type

Enterprises, Charging Solutions for Electric Vehicles

Requirements
Nice to have
• Bright, light design, clean, readable

```html
<!DOCTYPE html>
<html lang="de">
<head>
<meta charset="utf-8">
<title>Wendavo-Netz Professional – Flyer</title>
<link rel="stylesheet" href="https://fonts.googleapis.com/css2?family=Bebas+Neue&family=Montserrat:wght@400;500;600;700&display=swap">
<style>
:root{
  --green:#7cc24a;
  --green-dark:#5fa733;
  --green-soft:#a9d98a;
  --black:#0b0b0b;
  --white:#ffffff;
  --stage:#d4d5d7;
  --photo-grey:#8c8f8c;
}
*{box-sizing:border-box;margin:0;padding:0}
html,body{width:804px;height:1200px;overflow:hidden;background:var(--stage);font-family:"Montserrat",Arial,sans-serif;color:var(--black)}
.page{position:absolute;left:71px;width:663px;height:468px;background:var(--white);overflow:hidden}
.page--front{top:65px}
.page--back{top:630px}
.abs{position:absolute}
.display{font-family:"Bebas Neue",Impact,sans-serif;line-height:.9;letter-spacing:.5px}
.pill{position:absolute;background:var(--green);color:var(--white);font-weight:600;border-radius:10px;display:flex;align-items:center;padding-left:8px;white-space:nowrap}
.bar{position:absolute;background:var(--black);color:var(--white);font-weight:600;display:flex;align-items:center}
.photo{position:absolute}

/* front */
.front-title{left:15px;top:20px}
.front-title .brand{color:var(--green);font-size:45px}
.front-title .product{font-size:47px}
.audience{position:absolute;top:174px;width:60px;text-align:center;font-size:7.6px;font-weight:600;line-height:1.05}
.audience__box{width:50px;height:50px;margin:0 auto 10px;border:1.5px solid var(--green-soft);border-radius:4px;display:flex;align-items:center;justify-content:center}
.service-band{left:0;top:263px;width:400px;height:87px;background:linear-gradient(90deg,var(--green) 0%,var(--green-dark) 60%,rgba(124,194,74,.6) 100%);color:var(--white);padding:8px 13px}
.section-title{font-size:11px;font-weight:700;margin-bottom:5px}
.body-copy{font-size:7.6px;line-height:8.4px}
.body-copy .gap{display:block;height:3px}
.integration{left:13px;top:362px;width:345px}
.integration .section-title{color:var(--green);margin-bottom:4px}
.bottom-strip{left:0;top:455px;width:663px;height:13px;background:var(--green)}
.hero-photo{left:355px;top:0;width:308px;height:468px;clip-path:polygon(25% 0,100% 0,100% 100%,0 100%,12% 55%);background:linear-gradient(160deg,#b9bcb8 0%,var(--photo-grey) 45%,#9fcf7c 80%,#d9e26a 100%)}
.framed{border:6px solid var(--green);border-radius:10px}
.frame-a{left:380px;top:62px;width:151px;height:152px;background:linear-gradient(180deg,#9aa4a6,#8a6b52 60%,#6e8a55)}
.frame-b{left:502px;top:0;width:161px;height:150px;border-radius:0 0 0 10px;background:linear-gradient(90deg,#e8e8e6 0%,#c9c9c6 35%,#6d6f6b 60%,#8e8e8a 100%)}

/* back */
.logo{left:26px;top:20px;display:flex;flex-direction:column;align-items:center;gap:6px}
.logo__mark{width:26px;height:26px;border-radius:50%;background:var(--green)}
.logo__name{font-size:19px;font-weight:500}
.back-title{left:223px;top:22px;font-size:40px;white-space:nowrap}
.benefit-panel{left:12px;top:99px;width:638px;height:228px;border-radius:30px;background:linear-gradient(180deg,var(--green),#86c95a)}
.claim{left:0;top:108px;width:642px;height:66px;border-radius:0 33px 33px 0;padding-left:13px;display:block;padding-top:6px;font-size:15px;line-height:1.25}
.claim .accent{color:var(--green)}
.col{position:absolute;top:193px;color:var(--white);z-index:2}
.col h3{font-size:13.5px;font-weight:700;margin-bottom:8px;white-space:nowrap}
.col--benefits h3{font-size:12.3px;margin-top:1px;margin-bottom:9px}
.col li{list-style:none;font-size:8.8px;line-height:10.3px;margin-bottom:3.5px;display:flex;gap:4px}
.col li::before{content:"";flex:0 0 12px;height:5px;margin-top:3px;border:1.3px solid var(--black);border-radius:3px}
.divider{left:333px;top:190px;width:1px;height:115px;background:rgba(255,255,255,.6)}
.dark-area{left:247px;top:328px;width:416px;height:140px;background:var(--black)}
.thumb-a{left:266px;top:347px;width:100px;height:100px;background:linear-gradient(135deg,#eef4fa,#9fbcd6 60%,#d46a5a)}
.thumb-b{left:380px;top:347px;width:100px;height:100px;background:linear-gradient(180deg,#3f5f90,#7ea8d8 55%,#f4f2dc)}
.charger{left:500px;top:288px;width:133px;height:180px;background:linear-gradient(90deg,transparent 0%,#f0ede6 25%,#2b2f33 55%,#1d1f21 100%);clip-path:polygon(30% 6%,60% 0,100% 0,100% 100%,0 100%,0 35%)}
.contact-head{left:0;top:343px;width:163px;height:17px;border-radius:0 9px 9px 0;padding-left:13px;font-size:12px;font-weight:700}
.contact-copy{left:13px;top:361px;font-size:9.6px;line-height:1.2}
.consult{left:0;top:404px;width:222px;height:17px;border-radius:0 9px 9px 0;padding-left:13px;font-size:12px;font-weight:700}
.contact-lines{left:13px;top:423px;font-size:9.6px;line-height:1.2}
</style>
</head>
<body>

<section class="page page--front">
  <div class="abs front-title display">
    <div class="brand">WENDAVO-NETZ</div>
    <div class="product">PROFESSIONAL</div>
  </div>
  <div class="pill" style="left:15px;top:109px;width:165px;height:17px;font-size:10.5px">die Funktionen im Überblick</div>
  <div class="bar" style="left:0;top:138px;width:345px;height:27px;border-radius:0 14px 14px 0;padding-left:13px;font-size:15.5px">Verrechnung von Ladevorgängen für:</div>

  <div class="audience" style="left:13px"><div class="audience__box">
    <svg width="40" height="20" viewBox="0 0 40 20"><g fill="#222"><path d="M2 14l3-6h10l3 6v3H2z"/><path d="M22 14l3-6h10l3 6v3H22z"/><path d="M11 15l3-7h12l3 7v3H11z" fill="#000"/></g></svg>
  </div>Fuhrpark,<br>Dienstwagen</div>
  <div class="audience" style="left:89px;width:66px"><div class="audience__box">
    <svg width="36" height="24" viewBox="0 0 36 24"><g fill="#111"><circle cx="8" cy="6" r="4"/><circle cx="28" cy="6" r="4"/><circle cx="18" cy="9" r="4.5"/><path d="M1 18q7-8 14 0z"/><path d="M21 18q7-8 14 0z"/><path d="M9 23q9-11 18 0z"/></g></svg>
  </div>Mitarbeiter<br>Privatfahrzeuge</div>
  <div class="audience" style="left:170px"><div class="audience__box">
    <svg width="30" height="36" viewBox="0 0 30 36"><g fill="#111"><circle cx="8" cy="5" r="3"/><circle cx="15" cy="5" r="3"/><circle cx="22" cy="5" r="3"/><circle cx="5" cy="13" r="3"/><circle cx="15" cy="13" r="3"/><circle cx="25" cy="13" r="3"/><circle cx="10" cy="21" r="3"/><circle cx="20" cy="21" r="3"/><rect x="6" y="25" width="18" height="10" rx="3"/></g></svg>
  </div>Kunden und<br>Gäste</div>
  <div class="audience" style="left:246px"><div class="audience__box">
    <svg width="34" height="26" viewBox="0 0 34 26"><g fill="#111"><rect x="1" y="12" width="8" height="14"/><rect x="10" y="2" width="8" height="24"/><rect x="19" y="14" width="6" height="12"/><rect x="26" y="5" width="7" height="21"/></g></svg>
  </div>Vermieter,<br>Eigentümer</div>

  <div class="photo hero-photo" role="img" aria-label="Nahaufnahme eines Ladesteckers mit gelbem Kabel an einem Elektroauto"></div>
  <div class="photo framed frame-a" role="img" aria-label="Wallbox an einem Pfosten im Freien mit grünem Ladekabel"></div>
  <div class="photo framed frame-b" role="img" aria-label="Ladestation in einer Tiefgarage mit grünem Ladekabel"></div>

  <div class="abs service-band">
    <div class="section-title">Full-Service-Betreuung für sorgenfreies Management</div>
    <div class="body-copy">wendavo-netz übernimmt auf Wunsch alle organisatorischen Belange bei<br>der Verwaltung Ihrer Lade-Infrastruktur, einschließlich:<br>· Monitoring<br>· Support<br>· User-Onboarding und -Support<br>· Handling von Zugangskarten<br>· Integration von firmeninternen Zugangstoken</div>
  </div>

  <div class="abs integration">
    <div class="section-title">Perfekte Integration in kaufmännische Prozesse</div>
    <div class="body-copy">wendavo-netz fügt sich nahtlos in die kaufmännischen Strukturen moderner<br>Unternehmen ein und bietet:<span class="gap"></span>· Erweitertes Reporting<br>· Aufschlüsselung und Tarifierung nach Nutzergruppe<br>· Unterstützung unternehmensinterner Abrechnung und Verrechnung<br>&nbsp;&nbsp;und/oder Zahlungseinzug durch wendavo-netz<br>· Schnittstellen zu Buchhaltung und Lohnbuchhaltung<br>· Bedarfsgerechte Anpassbarkeit</div>
  </div>
  <div class="abs bottom-strip"></div>
</section>

<section class="page page--back">
  <div class="abs logo">
    <div class="logo__mark"></div>
    <div class="logo__name">wendavo-netz.de</div>
  </div>
  <div class="abs back-title display">WENDAVO-NETZ PROFESSIONAL</div>
  <div class="pill" style="left:243px;top:67px;width:381px;height:16px;font-size:10px;justify-content:center;padding-left:0">die maßgeschneiderte B2B-Abrechnungslösung für Elektromobilität</div>

  <div class="abs benefit-panel"></div>
  <div class="bar claim">Lade-Infrastruktur-Abrechnungslösungen für Unternehmen,<br>damit Lade-Infrastruktur Erträge statt Kosten produziert.<br><span class="accent">So wird Lade-Infrastruktur von einer Kostenstelle zu einem Profitcenter.</span></div>

  <div class="abs dark-area"></div>
  <div class="photo framed thumb-a" role="img" aria-label="Ladestecker an einem Fahrzeug in hellem Blau"></div>
  <div class="photo framed thumb-b" role="img" aria-label="Ladestation vor Solarpanelen und Sonnenlicht"></div>
  <div class="photo charger" role="img" aria-label="Wallbox mit grünem Ladekabel an dunkler Säule"></div>

  <div class="col" style="left:22px;width:300px">
    <h3>Leistungen:</h3>
    <ul>
      <li>Vielseitige Abrechnungsmöglichkeiten für<br>Fuhrpark, Mitarbeiter, Partnerunternehmen,<br>Mieter, Kunden und andere.</li>
      <li>Full-Service-Betreuung (Monitoring,<br>Abrechnung, Benutzerbetreuung)</li>
      <li>Integration in ihre Unternehmensabläufe</li>
      <li>Berücksichtigung von Eigentümer/Mieter-Konstellationen</li>
    </ul>
  </div>
  <div class="abs divider"></div>
  <div class="col col--benefits" style="left:364px;width:290px">
    <h3>Mit wendavo-netz Professional profitieren:</h3>
    <ul>
      <li>· Effizienter Verwaltung von Lade-Infrastruktur</li>
      <li>· Umfassende Full-Service-Betreuung</li>
      <li>· Nahtloser Integration in Ihre kaufmännischen<br>Prozesse</li>
      <li>· Vielseitigen Abrechnungsmöglichkeiten</li>
    </ul>
  </div>

  <div class="bar contact-head">Kontaktieren Sie uns</div>
  <div class="abs contact-copy">Erfahren Sie mehr über wendavo-netz<br>und wie wir Ihre Abrechnungsanforderungen<br>erfüllen können.</div>
  <div class="pill consult">für eine kostenlose Beratung:</div>
  <div class="abs contact-lines">Telefon: +49 (0) 30 555 0142<br>E-Mail: info@wendavo-netz.de<br>Web: www.wendavo-netz.de</div>
</section>

</body>
</html>
```